Law Offices business card

Hi there, I'll need business card for the Law Offices of Colin Matheny. The information must convey his strategic approach and quick resolution to complex business litigation needs. Please emphasize Civil Litigation, Corporate Law, Business Governance and Real Estate Law. Colin has over 25 years of experience in these fields.The card should be modern and edgy and the message should be clear. Please consult his current website for ideas.

```html
<!DOCTYPE html>
<html lang="en">
<head>
<meta charset="utf-8">
<title>Law Offices of Colin Matheny – Business Card</title>
<link rel="stylesheet" href="https://fonts.googleapis.com/css2?family=Tinos&family=Open+Sans:wght@400;600&display=swap">
<style>
  :root {
    --orange: #fc6a03;
    --white: #ffffff;
    --ink: #222222;
    --grey: #4a4a4a;
    --ring: #4d4d4d;
    --backdrop: #ecebe9;
  }
  * { box-sizing: border-box; margin: 0; padding: 0; }
  html, body { width: 1200px; height: 900px; overflow: hidden; }
  body { background: var(--backdrop); position: relative; font-family: "Open Sans", Arial, sans-serif; }

  .card { position: absolute; border-radius: 16px; overflow: hidden; }
  .card--front { left: 78px; top: 35px; width: 588px; height: 363px; background: var(--white); }
  .card--back { left: 390px; top: 506px; width: 565px; height: 350px; background: var(--orange); }

  .band { position: absolute; left: 0; right: 0; }
  .card--front .band { top: 28px; height: 99px; background: var(--orange); }
  .card--back .band { top: 81px; height: 96px; background: var(--white); }

  .mark { position: absolute; border-radius: 50%; display: flex; align-items: center; justify-content: center; font-family: "Tinos", "Times New Roman", serif; font-weight: 400; font-size: 21px; letter-spacing: 1px; color: var(--white); background: var(--orange); }
  .card--front .mark { left: 223px; top: 8px; width: 140px; height: 140px; border: 6px solid var(--ring); box-shadow: 0 0 0 6px var(--white); }
  .card--back .mark { left: 212px; top: 59px; width: 148px; height: 148px; box-shadow: inset 0 0 0 9px var(--orange), inset 0 0 0 13px var(--white); }

  .firm { position: absolute; left: 0; right: 0; text-align: center; font-family: "Tinos", "Times New Roman", serif; font-weight: 400; line-height: 1; }
  .firm__title, .firm__sub { display: block; transform: scaleX(0.86); }
  .card--front .firm { top: 150px; }
  .card--front .firm__title { color: var(--orange); font-size: 48px; }
  .card--front .firm__sub { color: var(--grey); font-size: 30px; margin-top: 1px; }
  .card--back .firm { top: 212px; }
  .card--back .firm__title { color: var(--white); font-size: 53px; }
  .card--back .firm__sub { color: var(--white); font-size: 34px; margin-top: 2px; }

  .practice { position: absolute; left: 0; right: 0; top: 302px; text-align: center; color: var(--white); font-size: 12.5px; line-height: 1.45; letter-spacing: 0.3px; }
  .practice__years { font-weight: 600; }

  .person { position: absolute; left: 22px; top: 234px; color: var(--ink); }
  .person__name { color: var(--orange); font-weight: 600; font-size: 21px; line-height: 1.2; }
  .person__role { font-size: 15px; margin-top: 1px; }
  .person__address { font-size: 15px; line-height: 1.45; margin-top: 13px; }

  .contacts { position: absolute; right: 34px; top: 241px; list-style: none; color: var(--ink); font-size: 15px; text-align: right; }
  .contacts li { display: flex; justify-content: flex-end; align-items: center; gap: 8px; height: 25px; }
  .contacts svg { width: 11px; height: 11px; fill: var(--orange); flex: none; }
</style>
</head>
<body>
  <section class="card card--front" aria-label="Business card front">
    <div class="band"></div>
    <div class="mark">MATHENY</div>
    <h1 class="firm">
      <span class="firm__title">LAW OFFICES</span>
      <span class="firm__sub">OF COLIN MATHENY</span>
    </h1>
    <div class="person">
      <p class="person__name">Colin Matheny</p>
      <p class="person__role">Attorney</p>
      <p class="person__address">318 Coral Terrace<br>Lakeview, Florida 33410</p>
    </div>
    <ul class="contacts">
      <li>561-555-0148
        <svg viewBox="0 0 12 12"><path d="M2.5 0.5l2 2.5-1.2 1.3c.7 1.6 2 2.9 3.6 3.6l1.3-1.2 2.5 2-1 2.3C5.2 11 1 6.8.3 1.5z"/></svg></li>
      <li>561-555-0192
        <svg viewBox="0 0 12 12"><path d="M1 3h10v8H1z M3 0h6v3H3z"/><rect x="3" y="6" width="6" height="1" fill="#fff"/><rect x="3" y="8" width="6" height="1" fill="#fff"/></svg></li>
      <li>colin@mathenylaw.com
        <svg viewBox="0 0 12 12"><path d="M0 2h12v8H0z"/><path d="M0.5 2.5L6 7l5.5-4.5" stroke="#fff" stroke-width="1" fill="none"/></svg></li>
      <li>www.mathenylaw.com
        <svg viewBox="0 0 12 12"><circle cx="6" cy="6" r="5.5"/><path d="M6 .5v11M.5 6h11M6 .5c-3 3-3 8 0 11M6 .5c3 3 3 8 0 11" stroke="#fff" stroke-width=".8" fill="none"/></svg></li>
    </ul>
  </section>

  <section class="card card--back" aria-label="Business card back">
    <div class="band"></div>
    <div class="mark">MATHENY</div>
    <h2 class="firm">
      <span class="firm__title">LAW OFFICES</span>
      <span class="firm__sub">OF COLIN MATHENY</span>
    </h2>
    <div class="practice">
      <p>Civil Litigation &middot; Corporate Law &middot; Business Governance &middot; Real Estate Law</p>
      <p class="practice__years">Over 25 Years of Experience</p>
    </div>
  </section>
</body>
</html>
```